Business Card Design for Property Development Company Director

I am looking for a professional and unforgettable business card design for our Director of our Property Development Company.
Please see attached .pptx file to find out what information to include. You don't have to follow the exact format shown in the file - I am interested to see your creative flair using the information provided.

```html
<!DOCTYPE html>
<html lang="en">
<head>
<meta charset="utf-8">
<title>Norvale Property Group — Business Card</title>
<link href="https://fonts.googleapis.com/css2?family=Montserrat:wght@400;500;600;700&display=swap" rel="stylesheet">
<style>
  :root {
    --backdrop: #3a3330;
    --card: #1c1d20;
    --blue: #1f5fbf;
    --white: #ffffff;
    --muted: #d9dbe0;
  }
  * { box-sizing: border-box; margin: 0; padding: 0; }
  html, body { width: 1200px; height: 716px; overflow: hidden; }
  body {
    background: var(--backdrop);
    font-family: "Montserrat", sans-serif;
    color: var(--white);
    position: relative;
  }
  .card {
    position: absolute;
    top: 204px;
    width: 540px;
    height: 308px;
    background: var(--card);
    overflow: hidden;
  }
  .card--front { left: 40px; }
  .card--back { left: 620px; }

  /* Brand lockup */
  .brand {
    display: flex;
    align-items: center;
    gap: 10px;
  }
  .brand__mark {
    width: 26px; height: 26px;
    background: var(--blue);
  }
  .brand__name {
    font-weight: 600;
    font-size: 22px;
    letter-spacing: 0.5px;
    color: var(--white);
    white-space: nowrap;
  }

  /* Front */
  .front__tagline {
    position: absolute;
    top: 40px; left: 0; right: 0;
    text-align: center;
    font-size: 14px;
    line-height: 1.35;
    color: var(--white);
  }
  .card--front .brand {
    position: absolute;
    top: 128px; left: 0; right: 0;
    justify-content: center;
  }
  .front__pitch {
    position: absolute;
    bottom: 44px; left: 0; right: 0;
    text-align: center;
    font-size: 13px;
    color: var(--white);
  }
  .front__pitch em { font-style: normal; color: var(--blue); font-weight: 500; }
  .card--front::after {
    content: "";
    position: absolute;
    left: 0; right: 0; bottom: 0;
    height: 6px;
    background: var(--blue);
  }

  /* Back */
  .card--back .brand {
    position: absolute;
    top: 34px; right: 30px;
  }
  .card--back .brand__name { font-size: 17px; }
  .card--back .brand__mark { width: 20px; height: 20px; }
  .person {
    position: absolute;
    top: 60px; left: 36px;
  }
  .person__name {
    font-size: 19px;
    font-weight: 500;
    color: var(--blue);
    text-transform: uppercase;
    letter-spacing: 0.3px;
  }
  .person__role { font-size: 13px; margin-top: 2px; }
  .rule {
    position: absolute;
    top: 126px; left: 36px; right: 30px;
    height: 1px;
    background: var(--blue);
  }
  .contacts {
    position: absolute;
    top: 140px; left: 36px;
    list-style: none;
    font-size: 13px;
    line-height: 1.6;
  }
  .contacts li { display: flex; align-items: center; gap: 8px; }
  .contacts svg { width: 10px; height: 10px; fill: var(--blue); flex: none; }
  .contacts b { font-weight: 700; }
  .licence {
    position: absolute;
    top: 104px; right: 30px;
    font-size: 10.5px;
    color: var(--white);
  }
  .licence span { color: var(--blue); font-weight: 600; }
  .address {
    position: absolute;
    bottom: 30px; right: 30px;
    text-align: right;
    font-size: 14px;
    line-height: 1.4;
  }
  .stripe {
    position: absolute;
    left: 0; right: 0; bottom: 0;
    height: 8px;
    display: flex;
  }
  .stripe__blue { width: 45%; background: var(--blue); }
  .stripe__white { flex: 1; background: var(--white); }
</style>
</head>
<body>

<section class="card card--front" aria-label="Card front">
  <p class="front__tagline">Property Development<br>&amp; Site Acquisition Specialists</p>
  <div class="brand">
    <span class="brand__mark"></span>
    <span class="brand__name">Norvale Property Group</span>
  </div>
  <p class="front__pitch">Ask me about our <em>INVESTMENT &amp; PARTNERSHIP</em> opportunities</p>
</section>

<section class="card card--back" aria-label="Card back">
  <div class="person">
    <h1 class="person__name">Daniel Marsh</h1>
    <p class="person__role">Director</p>
  </div>
  <div class="brand">
    <span class="brand__mark"></span>
    <span class="brand__name">Norvale Property Group</span>
  </div>
  <p class="licence"><span>Real Estate Lic:</span> 5512093 &amp; 5512094</p>
  <div class="rule"></div>
  <ul class="contacts">
    <li>
      <svg viewBox="0 0 10 10" aria-hidden="true"><path d="M2 0.5 L3.6 2.6 L2.8 3.6 Q3.8 5.8 6.2 7.2 L7.2 6.4 L9.5 8 L8.4 9.5 Q4 9 0.5 1.6 Z"/></svg>
      0400 123 456
    </li>
    <li>
      <svg viewBox="0 0 10 10" aria-hidden="true"><path d="M0.5 2 H9.5 V8 H0.5 Z M1.5 3 L5 5.5 L8.5 3" fill="none" stroke="#1f5fbf" stroke-width="1"/></svg>
      daniel@norvale.com.au
    </li>
    <li>
      <svg viewBox="0 0 10 10" aria-hidden="true"><circle cx="5" cy="5" r="4.5"/></svg>
      www.<b>norvale</b>.com.au
    </li>
  </ul>
  <address class="address" style="font-style:normal">42 Harlow St.<br>Fernbrook VIC 3999, Australia</address>
  <div class="stripe"><span class="stripe__blue"></span><span class="stripe__white"></span></div>
</section>

</body>
</html>
```